Inspiring Fundraising Foundation Website to Provide Academic Scholarships

Hello, we are launching a foundation to provide academic scholarships to high school students for college. We'd like this to be an informational website with contact information. There will be a total of approximately 5-7 pages in all.
The color scheme will be purple and white, with a girly feel. I 've attached the logo for reference!

Target Market(s)

high school students, college students

Industry/Entity Type

Education

Coding

Coded - Design and coding required

Number of Pages Required

5+ page

Font styles to use
Serif
Sans Serif
Script

Colors
6b449b
886aae
b7a5cd
e4daeb
ffffff
fdf9cf
fbf289

Requirements
Must have
• Purple, girly feel, to reflect the logo's style. Should be light-themed
Should not have
• No dark themes (aka heavy on black or dark colors)

```html
<!DOCTYPE html>
<html lang="en">
<head>
<meta charset="utf-8">
<title>Lorena Vance Foundation</title>
<link href="https://fonts.googleapis.com/css2?family=Roboto:wght@300;400;500;700&display=swap" rel="stylesheet">
<style>
:root{
  --purple:#6b449b;
  --purple-mid:#886aae;
  --lilac:#b7a5cd;
  --lilac-pale:#e4daeb;
  --white:#ffffff;
  --cream:#fdf9cf;
  --yellow:#fbf289;
  --grey-bg:#f4f4f6;
  --text:#333;
  --muted:#777;
  --line:#e2e2e2;
}
*{box-sizing:border-box;margin:0;padding:0}
html,body{width:1200px;height:2597px;overflow:hidden}
body{font-family:'Roboto',sans-serif;color:var(--text);background:var(--white);position:relative}
.page{position:relative;width:1200px;height:2597px}

/* header */
.site-header{position:absolute;top:0;left:0;width:1200px;height:123px;background:var(--white);border-top:4px solid var(--purple);z-index:2}
.contact-tab{position:absolute;top:0;right:0;width:540px;height:48px;background:var(--purple);clip-path:polygon(24px 0,100% 0,100% 100%,0 100%);display:flex;align-items:center;padding-left:52px;color:var(--white);font-size:16px;font-weight:500;gap:14px}
.contact-tab svg{width:15px;height:15px}
.social-top{display:flex;gap:7px;margin-left:36px}
.social-top span{width:30px;height:30px;border:1.5px solid var(--white);border-radius:50%}
.main-nav{position:absolute;top:80px;left:395px;display:flex;gap:0;font-size:12.5px;font-weight:500;color:#333}
.main-nav a{text-decoration:none;color:inherit;width:111px;text-align:center;display:block}
.main-nav a.active{color:var(--purple)}
.brand-badge{position:absolute;top:-40px;left:84px;width:180px;height:180px;border-radius:50%;background:var(--white);z-index:3;display:flex;flex-direction:column;align-items:center;justify-content:center;padding-top:36px;color:var(--purple);font-weight:700;font-size:21px;line-height:1.1;text-align:center}
.brand-badge small{display:block;font-size:11px;letter-spacing:3px;font-weight:700;margin-top:4px}

/* hero */
.hero{position:absolute;top:123px;left:0;width:1200px;height:492px;background:linear-gradient(120deg,#c9a27a 0%,#d86a6a 30%,#6f9bd3 55%,#e59bb3 80%,#c7b28f 100%)}
.hero-title{position:absolute;width:100%;top:268px;text-align:center;color:var(--white);text-shadow:0 2px 6px rgba(0,0,0,.35)}
.hero-title .first{display:block;font-size:50px;font-weight:300;color:var(--yellow);letter-spacing:1px}
.hero-title .second{display:block;font-size:50px;font-weight:500;margin-top:2px}
.hero-arrow{position:absolute;top:218px;width:52px;height:52px;border:2px solid var(--white);border-radius:50%;display:flex;align-items:center;justify-content:center}
.hero-arrow.prev{left:27px}.hero-arrow.next{right:26px}

/* welcome */
.welcome{position:absolute;top:615px;left:0;width:1200px;height:286px;text-align:center}
.section-title{color:var(--purple);font-size:24px;font-weight:500}
.welcome .section-title{margin-top:40px}
.divider{margin:12px auto 0;display:block}
.welcome p{width:750px;margin:16px auto 0;font-size:11.5px;line-height:26px;color:var(--muted)}
.btn{display:inline-block;background:var(--purple);color:var(--white);font-size:13px;font-weight:500;text-transform:uppercase;padding:0 24px;height:40px;line-height:40px;border-radius:3px}
.welcome .btn{margin-top:24px;width:158px;padding:0}

/* foundation */
.foundation{position:absolute;top:901px;left:0;width:1200px;height:637px;background:var(--grey-bg);text-align:center}
.foundation .section-title{margin-top:38px}
.foundation .lead{font-size:11.5px;color:var(--muted);margin-top:14px}
.cards{position:absolute;top:124px;left:87px;display:flex;gap:26px}
.card{width:326px;height:461px;background:var(--white);border:1px solid var(--line);text-align:left;position:relative}
.card-photo{height:217px}
.card h3{font-size:16px;font-weight:500;margin:24px 18px 0}
.card p{font-size:11.5px;color:var(--muted);line-height:22px;margin:12px 18px 0}
.progress{position:relative;margin:38px 18px 0;height:7px;background:var(--lilac-pale)}
.progress i{position:absolute;left:0;top:0;height:7px;width:75%;background:var(--purple)}
.progress b{position:absolute;top:-28px;left:68%;background:var(--purple);color:var(--white);font-size:11px;font-weight:500;padding:3px 7px}
.card-foot{position:absolute;bottom:0;left:0;right:0;height:50px;border-top:1px solid var(--line);display:flex;align-items:center;justify-content:space-between;padding:0 16px 0 18px}
.stars{display:flex;gap:2px}
.card-foot a{font-size:12px;font-weight:700;color:var(--purple);text-decoration:none}

/* scholarship band */
.scholarship{position:absolute;top:1538px;left:0;width:1200px;height:372px;background:linear-gradient(135deg,#7a53a8,#6b449b 60%,#7d5aac);color:var(--white)}
.scholarship h2{position:absolute;top:74px;left:87px;width:520px;font-size:27px;font-weight:400;line-height:42px}
.scholarship p{position:absolute;top:172px;left:87px;width:470px;font-size:11.5px;line-height:22px}
.btn-outline{position:absolute;top:270px;left:87px;width:171px;height:45px;border:1.5px solid var(--white);border-radius:2px;text-align:center;line-height:43px;font-size:13px;font-weight:500}
.stat{position:absolute;top:86px;width:160px;text-align:center}
.stat .ring{width:112px;height:112px;border:2px solid var(--white);border-radius:50%;margin:0 auto;display:flex;align-items:center;justify-content:center}
.stat strong{display:block;font-size:29px;font-weight:400;margin-top:16px}
.stat span{display:block;font-size:11.5px;font-weight:500;margin-top:2px}

/* about & team */
.about{position:absolute;top:1910px;left:87px;width:390px}
.about h2,.team h2{font-size:24px;font-weight:500;color:var(--purple);margin-top:30px}
.about p{font-size:11.5px;color:var(--muted);line-height:23px;margin-top:28px}
.about .btn{margin-top:26px;width:125px;padding:0;text-align:center}
.team{position:absolute;top:1910px;left:493px;width:622px}
.team-nav{position:absolute;top:36px;right:0;display:flex;gap:3px}
.team-nav span{width:18px;height:18px;background:#555;display:flex;align-items:center;justify-content:center}
.members{display:flex;gap:4px;margin-top:26px}
.member{width:204px;text-align:center}
.member .portrait{height:173px}
.member h4{font-size:13px;font-weight:700;margin-top:10px}
.member span{font-size:12px;color:var(--muted);display:block;margin-top:5px}

/* footer */
.site-footer{position:absolute;top:2269px;left:0;width:1200px;height:263px;background:var(--grey-bg)}
.footer-brand{position:absolute;top:62px;left:138px;color:var(--purple);font-size:34px;font-weight:700;line-height:1.05;text-align:center}
.footer-brand small{display:block;font-size:15px;letter-spacing:4px;font-weight:700;margin-top:8px}
.footer-col{position:absolute;top:50px}
.footer-col h5{font-size:16px;font-weight:500;color:#444}
.contact-list{list-style:none;margin-top:24px;font-size:12px;color:#666}
.contact-list li{display:flex;gap:12px;align-items:flex-start;margin-bottom:10px}
.contact-list svg{flex:none;width:12px;height:12px;margin-top:2px}
.contact-list u{color:#666}
.footer-col p{font-size:12px;color:#777;line-height:19px;margin-top:20px}
.email-field{margin-top:12px;width:208px;height:34px;border:1px solid #ccc;background:var(--white);font-size:12px;color:#666;padding:0 12px;line-height:32px}
.subscribe{margin-top:12px;display:inline-block;background:#555;color:var(--white);font-size:10px;padding:0 10px;height:27px;line-height:27px}
.follow-icons{display:flex;gap:8px;margin-top:18px}
.follow-icons span{width:34px;height:34px;border:1.5px solid #bbb;border-radius:50%}
.copyright{position:absolute;top:2532px;left:0;width:1200px;height:65px;background:var(--purple);color:var(--white);font-size:12.5px;text-align:center;line-height:65px}
</style>
</head>
<body>
<div class="page">

<header class="site-header">
  <div class="contact-tab">
    <svg viewBox="0 0 24 24" fill="#fff"><path d="M6.6 10.8a15 15 0 006.6 6.6l2.2-2.2c.3-.3.7-.4 1-.2 1.1.4 2.3.6 3.6.6.6 0 1 .4 1 1V20c0 .6-.4 1-1 1C10.6 21 3 13.4 3 4c0-.6.4-1 1-1h3.5c.6 0 1 .4 1 1 0 1.3.2 2.5.6 3.6.1.3 0 .7-.2 1z"/></svg>
    <span>CALL US : (000)-555-0142</span>
    <div class="social-top"><span></span><span></span><span></span><span></span><span></span></div>
  </div>
  <nav class="main-nav">
    <a class="active" href="#">HOME</a><a href="#">ABOUT US</a><a href="#">SERVICES</a><a href="#">FOUNDATION</a><a href="#">CAREERS</a><a href="#">NEWS</a><a href="#">CONTACT US</a>
  </nav>
</header>
<div class="brand-badge">Lorena<br>Vance<small>FOUNDATION</small></div>

<section class="hero">
  <div role="img" aria-label="Children doing crafts together around a classroom table" style="position:absolute;inset:0"></div>
  <div class="hero-arrow prev"><svg width="16" height="16" viewBox="0 0 16 16"><path d="M10 3L5 8l5 5" stroke="#fff" stroke-width="2" fill="none"/></svg></div>
  <div class="hero-arrow next"><svg width="16" height="16" viewBox="0 0 16 16"><path d="M6 3l5 5-5 5" stroke="#fff" stroke-width="2" fill="none"/></svg></div>
  <h1 class="hero-title"><span class="first">LORENA</span><span class="second">VANCE FOUNDATION</span></h1>
</section>

<section class="welcome">
  <h2 class="section-title">Welcome to Our Company</h2>
  <svg class="divider" width="74" height="14" viewBox="0 0 74 14"><line x1="0" y1="7" x2="74" y2="7" stroke="#d4b24a"/><circle cx="12" cy="7" r="5" fill="#fff" stroke="#d4b24a"/><circle cx="37" cy="7" r="5" fill="#fff" stroke="#d4b24a"/><circle cx="62" cy="7" r="5" fill="#fff" stroke="#d4b24a"/></svg>
  <p>Sed ut perspiciatis unde omnis iste natus error sit voluptatem accusantium doloremque laudantium, totam rem aperiam, eaque ipsa quae ab illo inventore veritatis et quasi architecto beatae vitae dicta sunt explicabo. Nemo enim ipsam voluptatem quia voluptas sit aspernatur aut odit aut fugit, sed quia consequuntur magni dolores eos qui ratione voluptatem sequi nesciunt.</p>
  <span class="btn">Read More Info</span>
</section>

<section class="foundation">
  <h2 class="section-title">Our Foundation</h2>
  <p class="lead">Sed ut perspiciatis unde omnis iste natus error sit voluptatem accusantium doloremque laudantium</p>
  <div class="cards">
    <article class="card">
      <div class="card-photo" role="img" aria-label="Young pupils working at desks in a busy classroom" style="background:linear-gradient(135deg,#d9c7c2,#c85c5c 50%,#e8e2dc)"></div>
      <h3>Sed ut perspiciatis unde omnis</h3>
      <p>Sed ut perspiciatis unde omnis iste natus error sit voluptatem accusantium doloremque laudantium, totam rem aperiam, eaque ipsa quae explicabo.</p>
      <div class="progress"><i></i><b>70%</b></div>
      <div class="card-foot"><div class="stars"><svg width="68" height="12" viewBox="0 0 68 12"><g fill="#f2b51b"><path id="s" d="M6 0l1.8 3.8 4.2.5-3.1 2.9.8 4.1L6 9.3 2.3 11.3l.8-4.1L0 4.3l4.2-.5z"/><use href="#s" x="14"/><use href="#s" x="28"/><use href="#s" x="42"/><use href="#s" x="56" opacity=".5"/></g></svg></div><a href="#">READ MORE</a></div>
    </article>
    <article class="card">
      <div class="card-photo" role="img" aria-label="Students raising hands in front of a chalkboard" style="background:linear-gradient(135deg,#3d4a3e,#7c8c5a 45%,#c9a0c9 75%,#d9b08a)"></div>
      <h3>Sed ut perspiciatis unde omnis</h3>
      <p>Sed ut perspiciatis unde omnis iste natus error sit voluptatem accusantium doloremque laudantium, totam rem aperiam, eaque ipsa quae explicabo.</p>
      <div class="progress"><i></i><b>70%</b></div>
      <div class="card-foot"><div class="stars"><svg width="68" height="12" viewBox="0 0 68 12"><g fill="#f2b51b"><use href="#s"/><use href="#s" x="14"/><use href="#s" x="28"/><use href="#s" x="42"/><use href="#s" x="56" opacity=".5"/></g></svg></div><a href="#">READ MORE</a></div>
    </article>
    <article class="card">
      <div class="card-photo" role="img" aria-label="A group of people joining hands in a circle" style="background:linear-gradient(135deg,#a8c2a0,#e0d9c8 40%,#c76a5a 70%,#6d89b8)"></div>
      <h3>Sed ut perspiciatis unde omnis</h3>
      <p>Sed ut perspiciatis unde omnis iste natus error sit voluptatem accusantium doloremque laudantium, totam rem aperiam, eaque ipsa quae explicabo.</p>
      <div class="progress"><i></i><b>70%</b></div>
      <div class="card-foot"><div class="stars"><svg width="68" height="12" viewBox="0 0 68 12"><g fill="#f2b51b"><use href="#s"/><use href="#s" x="14"/><use href="#s" x="28"/><use href="#s" x="42"/><use href="#s" x="56" opacity=".5"/></g></svg></div><a href="#">READ MORE</a></div>
    </article>
  </div>
</section>

<section class="scholarship">
  <h2>Academic scholarships to high school students for college</h2>
  <p>Sed ut perspiciatis unde omnis iste natus error sit voluptatem accusantium dolorem que laudantium, totam rem aperiam, eaque ipsa quae ab illo inventore veritatis et quasi architecto beatae vitae dicta sunt explicabo.</p>
  <div class="btn-outline">DONATE NOW!</div>
  <div class="stat" style="left:589px"><div class="ring"><svg width="26" height="34" viewBox="0 0 26 34"><text x="13" y="27" text-anchor="middle" font-family="Roboto,sans-serif" font-size="30" font-weight="700" fill="#fff">$</text></svg></div><strong>658</strong><span>DONATIONS TO CAUCUS</span></div>
  <div class="stat" style="left:786px"><div class="ring"><svg width="40" height="30" viewBox="0 0 40 30" fill="#fff"><path d="M20 2L0 11l20 9 20-9z"/><path d="M8 16v7c0 3 6 5 12 5s12-2 12-5v-7l-12 5z"/><rect x="35" y="11" width="2" height="11"/></svg></div><strong>985</strong><span>SCHOLARSHIP</span></div>
  <div class="stat" style="left:971px"><div class="ring"><svg width="40" height="28" viewBox="0 0 40 28" fill="#fff"><circle cx="20" cy="8" r="6"/><path d="M9 27c0-7 5-11 11-11s11 4 11 11z"/><circle cx="8" cy="11" r="4"/><path d="M0 25c0-5 3-8 8-8 1 0 2 0 3 .5C9 20 8 22 8 25z"/><circle cx="32" cy="11" r="4"/><path d="M40 25c0-5-3-8-8-8-1 0-2 0-3 .5 2 2.5 3 4.5 3 7.5z"/></svg></div><strong>526</strong><span>MEMBERS</span></div>
</section>

<section class="about">
  <h2>About Us</h2>
  <p>Sed ut perspiciatis unde omnis iste natus error sit voluptatem accusantium doloremque laudantium, totam rem aperiam, eaque ipsa quae ab illo inventore veritatis et quasi architecto beatae vitae dicta sunt explicabo. Nemo enim ipsam voluptatem quia voluptas sit aspernatur aut odit aut fugit, sed quia consequuntur magni dolores eos qui ratione volupta tem sequi aspernatur aut odit aut fugit voluptatem sequi nesciunt.</p>
  <span class="btn">Read More</span>
</section>

<section class="team">
  <h2>Our Teams</h2>
  <div class="team-nav"><span><svg width="8" height="8" viewBox="0 0 8 8"><path d="M5 1L2 4l3 3" stroke="#fff" fill="none"/></svg></span><span><svg width="8" height="8" viewBox="0 0 8 8"><path d="M3 1l3 3-3 3" stroke="#fff" fill="none"/></svg></span></div>
  <div class="members">
    <div class="member"><div class="portrait" role="img" aria-label="Portrait of team organiser" style="background:linear-gradient(180deg,#9a9a9a,#5a5a5a)"></div><h4>MARCUS HALE</h4><span>Organisor</span></div>
    <div class="member"><div class="portrait" role="img" aria-label="Portrait of team manager" style="background:linear-gradient(180deg,#8a8a8a,#6a5a52)"></div><h4>MARCUS HALE</h4><span>Manage</span></div>
    <div class="member"><div class="portrait" role="img" aria-label="Portrait of team co-ordinator" style="background:linear-gradient(180deg,#bdbdbd,#8a8a8a)"></div><h4>MARCUS HALE</h4><span>Co-Ordinater</span></div>
  </div>
</section>

<footer class="site-footer">
  <div class="footer-brand">Lorena<br>Vance<small>FOUNDATION</small></div>
  <div class="footer-col" style="left:391px">
    <h5>CONTACT US</h5>
    <ul class="contact-list">
      <li><svg viewBox="0 0 12 12" fill="#666"><path d="M1 4h10v7H1zM3 1h6v3H3z"/></svg>(000)-555-0142 (Phone)</li>
      <li><svg viewBox="0 0 12 12" fill="#666"><path d="M0 3h12v8H0zM3 0h6v3H3z"/></svg>(000)-555-0142 (Fax)</li>
      <li><svg viewBox="0 0 12 12"><rect x=".5" y="2" width="11" height="8" fill="none" stroke="#666"/><path d="M.5 2L6 7l5.5-5" fill="none" stroke="#666"/></svg><u>www.lorenavancefoundation.org</u></li>
      <li><svg viewBox="0 0 12 12" fill="#666"><path d="M6 0a4 4 0 014 4c0 3-4 8-4 8S2 7 2 4a4 4 0 014-4z"/></svg>3350 Lorem Ipsum Dummy Text<br>Lorem Ipsum</li>
    </ul>
  </div>
  <div class="footer-col" style="left:650px">
    <h5>NEWSLETTER</h5>
    <p>Register Your email address to get<br>information about us</p>
    <div class="email-field">Email Address</div>
    <span class="subscribe">SUBSCRIBE</span>
  </div>
  <div class="footer-col" style="left:903px">
    <h5>FOLLOW US</h5>
    <p>Lorem ipsum dolor sit amet, conse<br>ctetur adipiscing elit. Nulla in purus<br>nibh. Donec ornare</p>
    <div class="follow-icons"><span></span><span></span><span></span><span></span><span></span></div>
  </div>
</footer>
<div class="copyright">© Copyright 2017 Lorena Vance Foundation All Rights Reserved</div>

</div>
</body>
</html>
```